Design Startseite Kanzlei-Homepage
Zielgruppe
Wir sind eine Rechtsanwaltskanzlei in Kempten (Allgäu) und regional sowie überregional in verschiedenen Rechtsgebieten tätig. Unsere Zielgruppe sind sowohl private als auch gewerbliche Mandanten.
Aufgabenstellung
Die bestehende Gestaltung wirkt derzeit aus unserer Sicht überholt. Insbesondere soll das bislang dominierende Rot vollständig entfallen.
Stattdessen stellen wir uns ein modernes, hochwertiges Erscheinungsbild vor, primär in dunklen Farbtönen (Anthrazit/Schwarz) kombiniert mit Beige- bzw. warmen Naturtönen. Ziel ist eine klare visuelle Anlehnung an unsere Kanzleiräumlichkeiten (siehe Fotos).
Die Webseite soll insgesamt moderner, klarer und visuell anspruchsvoller wirken, ohne an Seriosität und Zugänglichkeit einzubüßen. Die Balance zwischen hochwertigem Erscheinungsbild und mandantenorientierter Nutzerführung steht für uns im Vordergrund.

```html
<!DOCTYPE html>
<html lang="de">
<head>
<meta charset="utf-8">
<title>Kanzlei am Lindenhof – Rechtsanwälte in Kempten</title>
<link href="https://fonts.googleapis.com/css2?family=Inter+Tight:wght@300;400;500;600&display=swap" rel="stylesheet">
<style>
:root{
  --ink:#111111;
  --dark:#1b1a18;
  --beige:#f5f1ec;
  --bronze:#a47c4f;
  --bronze-light:#c19b6c;
  --muted:#555;
  --white:#fff;
  --line:#d9d2c8;
}
*{box-sizing:border-box;margin:0;padding:0}
html,body{width:1200px;height:4624px;overflow:hidden}
body{position:relative;font-family:"Inter Tight",Arial,sans-serif;color:var(--ink);background:var(--white);font-size:11px;line-height:1.45}
.abs{position:absolute}
.eyebrow{font-size:11px;font-weight:500}
.h2{font-weight:300;font-size:30px;line-height:1.25;letter-spacing:-.3px}
.text{font-size:11px;line-height:1.5;color:#333}
.btn{display:inline-flex;align-items:center;height:30px;padding:0 18px;border-radius:16px;background:var(--ink);color:#fff;font-size:10px;font-weight:500}
.link{display:inline-flex;align-items:center;gap:10px;font-size:10px;font-weight:500;margin-left:18px}
.actions{display:flex;align-items:center}
.ph{position:absolute}
.tag{position:absolute;left:14px;bottom:14px;height:24px;padding:0 14px 0 24px;border-radius:12px;background:rgba(255,255,255,.25);color:#fff;font-size:9px;display:flex;align-items:center}
.tag::before{content:"";position:absolute;left:12px;width:5px;height:5px;border-radius:50%;background:#fff}

/* hero */
.hero{left:0;top:0;width:1200px;height:712px;background:linear-gradient(160deg,#5a4633 0%,#7a6650 35%,#3a332c 65%,#121212 100%)}
.nav{left:111px;top:22px;width:980px;display:flex;justify-content:space-between;align-items:center;color:#fff;z-index:2}
.brand{font-size:17px;font-weight:600;letter-spacing:.5px}
.menu{display:flex;gap:34px;font-size:11px}
.cta-circle{left:944px;top:136px;width:147px;height:147px;border-radius:50%;background:var(--bronze-light);color:#fff;display:flex;flex-direction:column;align-items:center;justify-content:center;font-size:14px;line-height:1.4;text-align:center;z-index:2}
.hero-title{left:111px;top:520px;width:760px;color:#fff;font-weight:300;font-size:40px;line-height:1.28;letter-spacing:-.5px;z-index:2}

/* services */
.services{left:0;top:712px;width:1200px;height:700px;background:var(--beige)}
.card{position:absolute;width:314px;height:104px;background:#fff;display:flex}
.card .img{width:104px;height:104px;flex:none}
.card .body{padding:10px 12px;position:relative;flex:1}
.card h3{font-size:11px;font-weight:600;margin-bottom:3px}
.card p{font-size:9.5px;line-height:1.45;color:#333}
.card svg{position:absolute;right:10px;bottom:10px}

/* team */
.team-bg{left:0;top:2004px;width:1200px;height:883px;background:var(--beige)}

/* review */
.review{position:absolute;width:330px;height:269px;background:#fff;padding:30px 26px;font-size:11px;line-height:1.5}
.review.faded{opacity:.35;overflow:hidden}

/* cta */
.cta-box{left:160px;top:3540px;width:864px;height:384px;background:var(--bronze)}
.btn-light{background:#fff;color:var(--bronze)}

/* footer */
.footer{left:0;top:4331px;width:1200px;height:293px;background:var(--ink);color:#fff}
.footer h4{font-size:10px;font-weight:400;color:#8c8c8c;margin-bottom:16px}
.footer p{font-size:11px;line-height:1.5}
</style>
</head>
<body>

<!-- Hero -->
<section class="abs hero" role="img" aria-label="Foto: Empfangsbereich der Kanzlei mit Holzwänden und beleuchtetem Tresen"></section>
<nav class="abs nav">
  <div class="brand">KANZLEI AM LINDENHOF</div>
  <div class="menu"><span>Startseite</span><span>Kanzlei</span><span>Rechtsgebiete</span><span>Kontakt</span></div>
</nav>
<div class="abs cta-circle">Jetzt Termin<br>vereinbaren
  <svg width="22" height="12" viewBox="0 0 22 12" style="margin-top:6px"><path d="M1 6h19M15 1l5 5-5 5" fill="none" stroke="#fff" stroke-width="1.2"/></svg>
</div>
<h1 class="abs hero-title">Rechtsanwälte und Fachanwälte in<br>Kempten: Kanzlei am Lindenhof</h1>
<svg class="abs" style="left:112px;top:650px" width="10" height="18" viewBox="0 0 10 18"><path d="M5 0v16M1 12l4 4 4-4" fill="none" stroke="#fff" stroke-width="1.2"/></svg>

<!-- Services -->
<section class="abs services"></section>
<div class="abs eyebrow" style="left:253px;top:803px">Ihr Recht. Unsere Aufgabe.</div>
<h2 class="abs h2" style="left:253px;top:830px;width:660px;font-size:31px;line-height:1.27">Wir vertreten Privatpersonen sowie nationale und internationale Unternehmen – kompromisslos, verlässlich und mit dem Blick fürs Wesentliche.</h2>
<p class="abs text" style="left:253px;top:957px;width:600px;font-size:10.5px">Ob es um familiäre Auseinandersetzungen, arbeitsrechtliche Konflikte oder komplexe Unternehmensstreitigkeiten geht – wir kennen die Materie, kennen die Gerichte und bringen Ihre Interessen klar auf den Punkt.</p>
<div class="abs actions" style="left:253px;top:1005px"><span class="btn">Mehr erfahren</span><span class="link"><svg width="16" height="8"><path d="M0 4h15M11 1l4 3-4 3" fill="none" stroke="#111"/></svg>Kontakt aufnehmen</span></div>

<div class="card" style="left:109px;top:1092px"><div class="img" role="img" aria-label="Foto: Familie" style="background:linear-gradient(135deg,#c9a98a,#8d7563)"></div><div class="body"><h3>Familienrecht</h3><p>Ehe und Scheidung, Umgangs- und Sorgerecht, Unterhaltszahlungen und mehr</p><svg width="16" height="8"><path d="M0 4h15M11 1l4 3-4 3" fill="none" stroke="#111"/></svg></div></div>
<div class="card" style="left:443px;top:1092px"><div class="img" role="img" aria-label="Foto: Waage und Vertrag" style="background:linear-gradient(135deg,#e6e2dc,#a8a39c)"></div><div class="body"><h3>Arbeitsrecht</h3><p>Kündigungen, Abmahnungen, Arbeitsverträge und Lohnansprüche, Mobbing und mehr</p><svg width="16" height="8"><path d="M0 4h15M11 1l4 3-4 3" fill="none" stroke="#111"/></svg></div></div>
<div class="card" style="left:777px;top:1092px"><div class="img" role="img" aria-label="Foto: Autos auf der Straße" style="background:linear-gradient(135deg,#8b8d8f,#4c4f52)"></div><div class="body"><h3>Verkehrsrecht</h3><p>Unfälle und Schadenersatz, Führerausweisentzug und Bussen, Strassenverkehrsdelikte und mehr</p><svg width="16" height="8"><path d="M0 4h15M11 1l4 3-4 3" fill="none" stroke="#111"/></svg></div></div>
<div class="card" style="left:109px;top:1218px"><div class="img" role="img" aria-label="Foto: Mietvertrag" style="background:linear-gradient(135deg,#f2eee8,#c9b7a4)"></div><div class="body"><h3>Miet- und Eigentumsrecht</h3><p>Mietverhältnisse, Eigentum und Hausordnung, Kündigungsschutz und mehr</p><svg width="16" height="8"><path d="M0 4h15M11 1l4 3-4 3" fill="none" stroke="#111"/></svg></div></div>
<div class="card" style="left:443px;top:1218px"><div class="img" role="img" aria-label="Foto: Gesetzbuch und Richterhammer" style="background:linear-gradient(135deg,#b06a32,#2f4a7a)"></div><div class="body"><h3>Erbrecht</h3><p>estamente und Erbverträge, Pflichtteile und Erbteilung, Nachlassregelung und mehr</p><svg width="16" height="8"><path d="M0 4h15M11 1l4 3-4 3" fill="none" stroke="#111"/></svg></div></div>
<div class="card" style="left:777px;top:1218px"><div class="img" role="img" aria-label="Foto: Justitia-Statue" style="background:linear-gradient(135deg,#e8e4de,#8a6a3d)"></div><div class="body"><h3>Strafrecht</h3><p>Strafverteidigung und Anklagevertretung, Einsprachen und Rechtsmittel, Opferhilfe und mehr</p><svg width="16" height="8"><path d="M0 4h15M11 1l4 3-4 3" fill="none" stroke="#111"/></svg></div></div>

<!-- Team -->
<section class="abs team-bg"></section>
<div class="abs eyebrow" style="left:111px;top:1552px">Gesichter hinter der Kanzlei</div>
<h2 class="abs h2" style="left:111px;top:1580px">Menschen, die Recht verstehen.</h2>
<p class="abs text" style="left:111px;top:1628px;width:410px;font-size:10.5px">Die Mitglieder unseres Anwaltsteams – jeweils ergänzt um ein ansprechend eingerichtetes und funktional ausgestattetes Sekretariat – spezialisieren sich in unterschiedliche Fachrichtungen, sodass für Sie eine große Bandbreite in der mandantenorientierten Rechtsberatung sichergestellt ist. Das gilt insbesondere für unsere Schwerpunkte im Verkehrsrecht und Strafrecht sowie im <u>Arbeitsrecht</u>, <u>Erbrecht</u>, <u>Mietrecht</u>, <u>Baurecht</u> und <u>Familienrecht</u>.<br><br>Auf die Mandatierung externer Anwälte kann durch die thematische Vielfalt und Spezialisierung unserer Juristen in den meisten Fällen verzichtet werden. Gleichzeitig gewährleistet unser engagiertes Kanzleiteam eine rechtliche Unterstützung ganz nach Ihren individuellen Interessen, stets auf dem neuesten Stand von Rechtsprechung und Praxis.</p>
<div class="abs actions" style="left:111px;top:1835px"><span class="btn">Kanzlei entdecken</span><span class="link"><svg width="16" height="8"><path d="M0 4h15M11 1l4 3-4 3" fill="none" stroke="#111"/></svg>Team kennenlernen</span></div>
<div class="ph" role="img" aria-label="Foto: Anwältin am Arbeitsplatz" style="left:576px;top:1502px;width:282px;height:348px;background:linear-gradient(160deg,#e9e9e7,#9a9a96 70%,#3a3a3a)"><span class="tag">Petra Beispiel</span></div>
<div class="ph" role="img" aria-label="Foto: Gruppenbild des Teams" style="left:874px;top:1586px;width:163px;height:117px;background:linear-gradient(160deg,#c9cacb,#55575a)"></div>
<div class="ph" role="img" aria-label="Foto: Beratungsgespräch im Besprechungsraum" style="left:874px;top:1717px;width:217px;height:271px;background:linear-gradient(160deg,#dfe3e4,#7d7570 60%,#2e3340)"><span class="tag">Lena Beispiel</span></div>
<div class="ph" role="img" aria-label="Foto: Empfangstresen der Kanzlei" style="left:646px;top:1866px;width:212px;height:260px;background:linear-gradient(180deg,#d7d7d5,#6e6a64 55%,#26231f)"></div>

<!-- Reviews -->
<div class="review faded" style="left:111px;top:2239px;width:65px;padding:22px 0 0 6px;color:#777">Kanzlei<br><br><br>der als<br>ne<br>legen</div>
<div class="review" style="left:197px;top:2239px;font-size:10.5px">»Seit Jahren ist die Kanzlei am Lindenhof (vormals Kanzlei Brenner) unser Begleiter in rechtlichen Angelegenheiten. Egal ob es Fragen im Verkehrsrecht, im Bereich des Arbeitsrechts oder als Inkasso bei Forderungen gegen Kunden sind. Wir wurden bisher sehr gut betreut und unsere Anliegen wurden zeitnah und professionell erledigt. Wir freuen uns einen starken Partner für alle Rechtsfragen gefunden zu haben und hoffen weiterhin auf eine gute Zusammenarbeit.«
  <div style="position:absolute;left:26px;bottom:20px">H. Torsysteme GmbH<br>★★★★★ via Bewertungsportal</div></div>
<div class="review faded" style="left:551px;top:2239px;width:65px;padding:22px 0 0 20px;color:#777">»Seit J<br>Brenn<br>Angel<br>Verke<br>Inkas<br>wurde<br>freue<br>Recht<br>weite<br><br>H. Tor<br>★★★</div>
<svg class="abs" style="left:338px;top:2530px" width="50" height="10"><path d="M13 5H1M5 1L1 5l4 4M37 5h12M45 1l4 4-4 4" fill="none" stroke="#111"/></svg>
<div class="abs eyebrow" style="left:694px;top:2289px">Was unsere Mandanten sagen</div>
<h2 class="abs h2" style="left:694px;top:2316px">Referenzen</h2>
<p class="abs text" style="left:694px;top:2372px;width:400px;font-size:10.5px">Was unsere Mandanten sagen, zählt mehr als jede Eigenwerbung. Lesen Sie, warum Menschen und Unternehmen uns wieder und wieder vertrauen.</p>
<div class="abs actions" style="left:694px;top:2425px"><span class="btn">Weitere Rezensionen</span><span class="link"><svg width="16" height="8"><path d="M0 4h15M11 1l4 3-4 3" fill="none" stroke="#111"/></svg>Kontakt aufnehmen</span></div>

<!-- Video -->
<div class="ph" role="img" aria-label="Video-Standbild: Das gesamte Kanzleiteam auf einem gepflasterten Platz" style="left:99px;top:2635px;width:1033px;height:501px;background:linear-gradient(170deg,#8e8e8c,#575655 60%,#2b2b2b)">
  <span class="tag" style="top:18px;bottom:auto">Film ab: Das ist Kanzlei am Lindenhof</span>
  <svg class="abs" style="left:479px;top:213px" width="75" height="75"><circle cx="37.5" cy="37.5" r="37.5" fill="#a47c4f" opacity=".9"/><path d="M30 25l20 12.5L30 50z" fill="#fff"/></svg>
</div>

<!-- Strength -->
<div class="abs eyebrow" style="left:361px;top:3226px">Juristische Stärke auf einer Hand</div>
<h2 class="abs h2" style="left:361px;top:3254px">Lorem Ipsum</h2>
<p class="abs text" style="left:361px;top:3308px;width:480px;font-size:10.5px">Lorem ipsum dolor sit amet, consetetur sadipscing elitr, sed diam nonumy eirmod tempor invidunt ut labore et dolore magna aliquyam erat, sed diam voluptua. At vero eos et accusam et justo duo dolores et ea rebum. Stet clita kasd gubergren, no sea takimata sanctus est Lorem ipsum dolor sit amet. Lorem ipsum dolor sit amet, consetetur sadipscing elitr, sed diam nonumy eirmod tempor invidunt ut labore et dolore magna aliquyam erat, sed diam voluptua.</p>
<div class="abs actions" style="left:361px;top:3417px"><span class="btn">Kontakt aufnehmen</span><span class="link"><svg width="16" height="8"><path d="M0 4h15M11 1l4 3-4 3" fill="none" stroke="#111"/></svg>Mehr erfahren</span></div>

<!-- CTA -->
<section class="abs cta-box"></section>
<div class="ph" role="img" aria-label="Porträtfoto eines Anwalts" style="left:213px;top:3588px;width:236px;height:235px;background:radial-gradient(circle at 50% 40%,#6b5a4c,#1c1c1c 70%)"><span class="tag">Jonas Beispiel</span></div>
<div class="abs eyebrow" style="left:504px;top:3610px;color:#fff">Jetzt handeln – nicht warten</div>
<h2 class="abs h2" style="left:504px;top:3640px;color:#fff;width:500px">Kein Fall zu gross. Kein Anliegen zu klein: Wir sind in jedem Fall für Sie da.</h2>
<p class="abs text" style="left:504px;top:3724px;width:470px;color:#f1e6d8;font-size:10.5px">Jonas Beispiel steht Ihnen persönlich zur Seite – für eine erste Einschätzung, die keine Fragen offen lässt.</p>
<div class="abs actions" style="left:504px;top:3772px"><span class="btn btn-light">Jetzt anrufen</span><span class="link" style="color:#fff"><svg width="16" height="8"><path d="M0 4h15M11 1l4 3-4 3" fill="none" stroke="#fff"/></svg>E-Mail schreiben</span></div>

<!-- Map -->
<div class="ph" role="img" aria-label="Karte: Stadtgebiet Kempten mit Standort der Kanzlei" style="left:0;top:3961px;width:1200px;height:370px;background:linear-gradient(180deg,#f1f1f1,#e6e6e6)"></div>
<svg class="abs" style="left:584px;top:4094px" width="24" height="32"><path d="M12 0C5 0 0 5 0 12c0 9 12 20 12 20s12-11 12-20C24 5 19 0 12 0z" fill="#a47c4f"/><circle cx="12" cy="12" r="4" fill="#fff"/></svg>
<div class="abs" style="left:481px;top:4146px;width:229px;height:74px;background:#fff;display:flex;box-shadow:0 2px 8px rgba(0,0,0,.08)">
  <div role="img" aria-label="Foto: Kanzleigebäude" style="width:72px;height:74px;background:linear-gradient(160deg,#d9d6d1,#7a746d)"></div>
  <div style="padding:12px 10px;font-size:10px;position:relative;flex:1"><b style="font-weight:500">In Kempten Zuhause</b><br>Jetzt Anfahrt berechnen
    <svg style="position:absolute;right:10px;bottom:10px" width="16" height="8"><path d="M0 4h15M11 1l4 3-4 3" fill="none" stroke="#111"/></svg></div>
</div>
<div class="abs" style="left:1168px;top:4264px;width:22px;height:56px;background:#fff;font-size:12px;text-align:center;line-height:18px">+<br>−<br>↑</div>

<!-- Footer -->
<footer class="abs footer">
  <div class="abs brand" style="left:108px;top:66px;font-size:24px;letter-spacing:.8px">KANZLEI AM LINDENHOF</div>
  <div class="abs" style="left:642px;top:68px"><h4>Kontakt</h4><p>Kanzlei am Lindenhof<br>Mühlbachweg 14<br>87439 Kempten<br><br>Tel: 0831 - 540 217 90<br>info@kanzlei-lindenhof.de</p></div>
  <div class="abs" style="left:850px;top:68px"><h4>Rechtsgebiete</h4><p>Familienrecht<br>Verkehrsrecht<br>Arbeitsrecht<br>Erbrecht<br>Strafrecht<br>Miet- / Wohneigentumsrecht</p></div>
  <svg class="abs" style="left:1080px;top:60px" width="10" height="36"><path d="M5 36V2M1 6l4-4 4 4" fill="none" stroke="#fff"/></svg>
  <div class="abs" style="left:108px;top:236px;font-size:10px">Kanzlei am Lindenhof © All rights reserved.</div>
  <div class="abs" style="left:954px;top:236px;font-size:10px;display:flex;gap:14px"><span>Impressum</span><span>Datenschutz</span></div>
</footer>

</body>
</html>
```